Boutique custom software development company needs new business card

Our nearly 20 year old custom software development company would like to better include the fact that we are now providing Bitcoin services. These new services are B2B include education (how to acquire and securely hold Bitcoin) and integrating Bitcoin payments into existing ecommerce sites or other existing systems. Please keep the card clean and simple. Attached is our current design and some other files. vextorial.com

Target Market(s)

businesses owners interested in long term relationship

Industry/Entity Type

Custom software development and Bitcoin

Contact Information for Business Card

Dale Parker, dale@vextorial.com, vextorial.com, (888) 555-VXTRL

Font styles to use
Other font styles liked:
• monospace

Requirements
Must have
• double-sided
Nice to have
• clean and simple
Should not have
• physical address

```html
<!DOCTYPE html>
<html lang="en">
<head>
<meta charset="utf-8">
<title>Vextorial business card</title>
<link rel="stylesheet" href="https://fonts.googleapis.com/css2?family=Montserrat:wght@400;700;800&display=swap">
<style>
  :root {
    --bg: #3b3b3b;
    --card: #141414;
    --blue: #3f74c8;
    --orange: #f07a1f;
    --text: #e8e8e8;
    --muted: #9aa3b0;
    --emboss: #262626;
  }
  * { margin: 0; padding: 0; box-sizing: border-box; }
  html, body { width: 1200px; height: 801px; overflow: hidden; }
  body {
    background: var(--bg);
    font-family: "Montserrat", Arial, sans-serif;
    display: flex;
    align-items: center;
    justify-content: center;
    gap: 40px;
  }
  .card {
    position: relative;
    width: 520px;
    height: 297px;
    background: var(--card);
    border-bottom: 3px solid var(--blue);
    border-left: 2px solid var(--blue);
    box-shadow: 0 10px 24px rgba(0,0,0,.35);
  }
  .brand {
    position: absolute;
    left: 34px;
    top: 40px;
  }
  .brand-row { display: flex; align-items: center; gap: 9px; }
  .brand-mark { width: 22px; height: 22px; background: var(--orange); }
  .brand-name {
    font-weight: 800;
    font-size: 32px;
    letter-spacing: -0.5px;
    color: var(--blue);
    line-height: 1;
  }
  .tagline {
    margin-top: 6px;
    font-size: 12px;
    color: var(--blue);
    letter-spacing: -0.2px;
  }
  .person {
    position: absolute;
    right: 24px;
    top: 96px;
    text-align: right;
  }
  .person-name {
    font-weight: 700;
    font-size: 18px;
    color: var(--blue);
    letter-spacing: 0.5px;
    line-height: 1.1;
  }
  .services {
    margin-top: 4px;
    font-size: 11px;
    color: var(--muted);
    letter-spacing: 0.3px;
  }
  .divider {
    position: absolute;
    left: 34px;
    right: 16px;
    top: 148px;
    height: 1px;
    background: var(--blue);
  }
  .contacts {
    position: absolute;
    left: 34px;
    top: 200px;
    list-style: none;
    font-size: 14px;
    color: var(--text);
    line-height: 23px;
  }
  .contacts li { display: flex; align-items: center; gap: 10px; }
  .contacts svg { width: 12px; height: 12px; flex: none; }
  .back-mark {
    position: absolute;
    inset: 0;
    display: flex;
    flex-direction: column;
    align-items: center;
    justify-content: center;
    gap: 14px;
  }
  .back-mark .brand-row { gap: 12px; }
  .back-mark .brand-mark { background: var(--emboss); width: 34px; height: 34px; }
  .back-mark .brand-name { color: var(--emboss); font-size: 46px; }
  .back-services {
    font-size: 12px;
    color: #3a3a3a;
    letter-spacing: 2px;
    text-transform: uppercase;
  }
</style>
</head>
<body>
  <section class="card card-front">
    <div class="brand">
      <div class="brand-row">
        <span class="brand-mark"></span>
        <span class="brand-name">VEXTORIAL</span>
      </div>
      <p class="tagline">developer of custom applications</p>
    </div>
    <div class="person">
      <p class="person-name">DALE PARKER</p>
      <p class="services">Bitcoin education &amp; payment integration</p>
    </div>
    <div class="divider"></div>
    <ul class="contacts">
      <li>
        <svg viewBox="0 0 16 16" aria-hidden="true"><path fill="#f07a1f" d="M3 1l3 3-1.5 2a8 8 0 0 0 5.5 5.5L12 10l3 3-2 2C7 15 1 9 1 3z"/></svg>
        (888) 555-VXTRL
      </li>
      <li>
        <svg viewBox="0 0 16 16" aria-hidden="true"><rect x="1" y="3" width="14" height="10" fill="#f07a1f"/><path d="M1 3l7 6 7-6" fill="none" stroke="#141414" stroke-width="1.5"/></svg>
        dale@vextorial.com
      </li>
      <li>
        <svg viewBox="0 0 16 16" aria-hidden="true"><circle cx="8" cy="8" r="6.5" fill="none" stroke="#f07a1f" stroke-width="2"/><path d="M1.5 8h13M8 1.5c-3 3.5-3 9.5 0 13M8 1.5c3 3.5 3 9.5 0 13" fill="none" stroke="#f07a1f" stroke-width="1.3"/></svg>
        vextorial.com
      </li>
    </ul>
  </section>

  <section class="card card-back">
    <div class="back-mark">
      <div class="brand-row">
        <span class="brand-mark"></span>
        <span class="brand-name">VEXTORIAL</span>
      </div>
      <p class="back-services">Custom software &middot; Bitcoin services</p>
    </div>
  </section>
</body>
</html>
```